professional business card design for technology company

We are a small technology consulting firm, specialising in consulting based around Cloud and Managed services. Our colour scheme is yellow, blue and white, as you can see in the logos. Although we are based in melbourne australia, due to the nature of our work, our clients can be located anywhere. We are looking for a clean, professional, positive look - similar to our company logo

Target Market(s)

small business

Industry/Entity Type

Business

Contact Information for Business Card

eye catching, designed to incorporate some level of raised printing. Must contain website address, phone number, name and job title

Requirements
Must have
• Logo (attached) - use of the same colour scheme

```html
<!DOCTYPE html>
<html lang="en">
<head>
<meta charset="utf-8">
<title>Cirrolux Business Card</title>
<link href="https://fonts.googleapis.com/css2?family=Raleway:wght@300;400;700&display=swap" rel="stylesheet">
<style>
  :root {
    --backdrop: #cad4d2;
    --card: #1d232b;
    --yellow: #f5e20a;
    --blue: #3fc8f4;
    --white: #ffffff;
    --soft-white: #d9dde2;
  }
  * { margin: 0; padding: 0; box-sizing: border-box; }
  html, body {
    width: 1200px;
    height: 900px;
    overflow: hidden;
    background: var(--backdrop);
    font-family: "Raleway", sans-serif;
  }
  .canvas {
    position: relative;
    width: 1200px;
    height: 900px;
  }
  .card {
    position: absolute;
    background: var(--card);
    border-radius: 18px;
  }
  .card-front {
    left: 313px; top: 65px;
    width: 592px; height: 344px;
    display: flex;
    align-items: center;
    justify-content: center;
    gap: 18px;
  }
  .brand-dot {
    width: 34px; height: 34px;
    border-radius: 50%;
    background: var(--yellow);
  }
  .brand-name {
    font-family: "Raleway", sans-serif;
    font-weight: 700;
    font-size: 60px;
    color: var(--yellow);
    letter-spacing: -1px;
  }
  .card-back {
    left: 313px; top: 465px;
    width: 585px; height: 340px;
  }
  .back-brand {
    position: absolute;
    left: 42px; top: 248px;
    font-weight: 700;
    font-size: 30px;
    color: var(--blue);
  }
  .holder-name {
    position: absolute;
    left: 307px; top: 138px;
    font-size: 30px;
    font-weight: 400;
    color: var(--white);
  }
  .holder-name .surname { font-weight: 300; color: var(--soft-white); }
  .holder-title {
    position: absolute;
    left: 308px; top: 174px;
    font-size: 15px;
    color: var(--yellow);
  }
  .contact {
    position: absolute;
    left: 364px; top: 206px;
    font-size: 15px;
    line-height: 20px;
    color: var(--soft-white);
    list-style: none;
  }
</style>
</head>
<body>
<main class="canvas">
  <section class="card card-front">
    <span class="brand-dot"></span>
    <span class="brand-name">Cirrolux</span>
  </section>

  <section class="card card-back">
    <span class="back-brand">Cirrolux</span>
    <h1 class="holder-name">Daniel <span class="surname">Reyes</span></h1>
    <p class="holder-title">Managing Director</p>
    <ul class="contact">
      <li>hello@cirrolux.com</li>
      <li>044-987 654 321</li>
    </ul>
  </section>
</main>
</body>
</html>
```